Provide bookkeeping and accounting services to small and growing businesses

We need website and logo design using the name Dornaby as the logo.
The target audience are small companies and startups who need:
1) Simple bookkeeping services
2) Accounting advice that only someone with many years of senior financial experience as a CPA can provide.

The services are provided by two individuals. each of whom specialize in one of the areas.

We want the website to be clean without a lot of visual distraction but don't know how to make a boring subject interesting. We believe our potential clients, small business owners, need to find what they want quickly and easily without a lot of verbiage or distractions.

We've attached a draft of the homepage and have completed the text on most of the other pages.

Target Market(s)

small and early stage growth companies in San Diego North County

Industry/Entity Type

Accounting

Number of Pages Required

1 page

Font styles to use
Sans Serif

Colors
86cfc6
33b8a4
85cae6

Requirements
Must have
• We need a design for the website homepage that includes the name Dornaby as the logo. Must include a design for the name.
• Must have color in teal or greenish blue.
Nice to have
• White background, clean, clear, uncluttered.
• We would like to use the design in a Theme on a WordPress website. Themes Paper Lantern and Quiet Harbour are appealing to us.
Should not have
• Moving pictures

```html
<!DOCTYPE html>
<html lang="en">
<head>
<meta charset="utf-8">
<title>Dornaby Bookkeeping</title>
<link href="https://fonts.googleapis.com/css2?family=Raleway:wght@400;500;600;700&family=Roboto:wght@300;400;500&family=Arapey&display=swap" rel="stylesheet">
<style>
:root{
  --teal:#33b8a4;
  --teal-soft:#86cfc6;
  --sky:#6db9df;
  --ink:#222;
  --text:#555;
  --muted:#888;
  --light:#f2f2f2;
  --line:#dcdcdc;
  --footer:#363f3e;
  --footer-text:#d8dcdb;
  --white:#fff;
}
*{margin:0;padding:0;box-sizing:border-box}
html,body{width:1200px;height:2378px;overflow:hidden}
body{font-family:'Roboto',sans-serif;color:var(--text);background:var(--white);font-size:13px;position:relative}
a{color:inherit;text-decoration:none}
.wrap{width:1038px;margin:0 auto;position:relative}

/* hero */
.hero{position:relative;height:567px;overflow:hidden;color:var(--white)}
.hero-photo{position:absolute;inset:0;background:linear-gradient(110deg,#5b6168 0%,#7a8189 35%,#8d949c 60%,#5c6570 100%)}
.hero-shade{position:absolute;inset:0;background:linear-gradient(180deg,rgba(20,24,28,.55),rgba(20,24,28,.35) 40%,rgba(20,24,28,.45))}
.site-header{position:absolute;top:20px;left:81px;right:76px;display:flex;justify-content:space-between;align-items:flex-start}
.logo{display:flex;align-items:center;gap:10px;margin-top:8px}
.logo-mark{width:22px;height:22px;background:var(--teal);display:block}
.logo-name{font-family:'Raleway',sans-serif;font-weight:600;font-size:22px;color:var(--white);letter-spacing:.3px}
.main-nav{display:flex;margin-top:14px}
.main-nav a{font-family:'Raleway',sans-serif;font-weight:500;font-size:14px;margin-left:52px;padding-bottom:8px}
.main-nav a.active{color:var(--teal);border-bottom:2px solid var(--teal)}
.hero-copy{position:absolute;top:244px;left:0;right:0;text-align:center}
.hero-copy h1{font-family:'Arapey',serif;font-weight:400;font-size:37px;letter-spacing:.3px}
.hero-copy p{font-family:'Raleway',sans-serif;font-size:16px;color:#d6d9dc;margin-top:4px}
.btn-hero{display:inline-flex;align-items:center;gap:16px;margin-top:40px;height:39px;width:296px;justify-content:center;background:var(--teal);border-radius:20px;font-weight:500;font-size:15px;color:var(--white)}

/* about */
.about{height:362px;border-bottom:1px solid var(--line)}
.about .wrap{display:flex;padding-top:45px}
.about-text{width:628px}
.section-title{font-family:'Raleway',sans-serif;font-weight:500;font-size:27px;color:var(--ink)}
.section-title em{font-style:normal;color:var(--teal)}
.about-text p{font-size:12.5px;line-height:24px;color:var(--text);text-align:justify;margin-top:14px}
.about-text p + p{margin-top:4px}
.btn-more{display:inline-flex;align-items:center;gap:14px;margin-top:20px;background:#d9d9d9;color:#444;font-size:12.5px;padding:0 16px;height:32px}
.about-divider{width:1px;background:var(--line);margin:0 46px 0 47px;height:276px}
.features{display:flex;flex-direction:column;gap:30px;padding-top:6px}
.feature{display:flex;gap:22px}
.feature-icon{width:50px;height:50px;background:var(--teal);display:flex;align-items:center;justify-content:center;flex:none}
.feature h3{font-family:'Raleway',sans-serif;font-weight:600;font-size:16px;color:var(--ink);margin-top:-6px}
.feature p{font-size:12px;line-height:19px;color:var(--text);width:250px;margin-top:4px}

/* services */
.services{background:var(--light);height:441px;text-align:center;padding-top:36px}
.section-sub{font-size:13px;color:#444;margin-top:8px}
.service-cards{display:flex;gap:22px;margin-top:31px;text-align:left}
.service-card{width:243px;height:257px;background:var(--white);position:relative}
.service-photo{height:135px}
.photo-a{background:linear-gradient(135deg,#2a5fa8,#6b8fc3 55%,#c9cfd6)}
.photo-b{background:linear-gradient(135deg,#d9dbde,#f1f1f1 50%,#8a8f96)}
.photo-c{background:linear-gradient(135deg,#a9c4dd,#6d7f95 50%,#d6a7a4)}
.photo-d{background:linear-gradient(135deg,#3b4a63,#8fa6c4 50%,#e6eaf0)}
.service-card h3{font-family:'Raleway',sans-serif;font-weight:500;font-size:16.5px;color:var(--teal);margin:13px 18px 0}
.service-card p{font-size:11.5px;line-height:19px;color:#444;margin:6px 18px 0}
.corner{position:absolute;right:0;bottom:0}

/* call band */
.cta-band{background:var(--sky);height:89px;color:var(--white)}
.cta-band .wrap{display:flex;align-items:center;height:100%}
.cta-band p{font-family:'Raleway',sans-serif;font-weight:600;font-size:16px;line-height:25px;width:530px}
.cta-phone{font-size:15.5px;margin-left:120px}
.btn-contact{margin-left:auto;display:inline-flex;align-items:center;gap:14px;justify-content:center;width:190px;height:38px;background:var(--white);color:#333;border-radius:20px;font-size:15px;font-weight:500}

/* testimonials */
.clients{height:553px;text-align:center;padding-top:40px}
.testimonials{display:flex;justify-content:space-between;margin-top:54px;padding:0 20px}
.testimonial{width:280px}
.avatar{width:86px;height:86px;border-radius:50%;margin:0 auto;border:2px solid #e6e6e6}
.av-1{background:radial-gradient(circle at 50% 40%,#d9a98c,#6b3f2c 75%)}
.av-2{background:radial-gradient(circle at 50% 40%,#e0b89c,#c5cfd8 75%)}
.av-3{background:radial-gradient(circle at 50% 40%,#dcae93,#4f3428 75%)}
.testimonial blockquote{font-size:12.5px;line-height:23px;color:#444;margin:30px auto 0;width:270px}
.quote-rule{width:58px;height:1px;background:#bbb;margin:18px auto 0}
.testimonial cite{display:block;font-style:normal;font-size:14px;color:#333;margin-top:16px}
.testimonial cite b{color:var(--teal);font-weight:500}
.partner-strip{border-top:1px solid var(--line);margin-top:40px;display:flex;justify-content:space-between;align-items:center;padding-top:38px}
.partner{display:flex;align-items:center;gap:8px;font-family:'Raleway',sans-serif;font-weight:600;font-size:24px;color:#4a4a4a}
.partner i{width:13px;height:13px;border-radius:50%;background:#4a4a4a;display:block}

/* footer */
.site-footer{background:var(--footer);height:855px;color:var(--footer-text)}
.footer-cols{display:flex;padding-top:50px;height:309px}
.footer-col h4{font-family:'Raleway',sans-serif;font-weight:500;font-size:21px;color:var(--teal);margin-bottom:20px}
.footer-col ul{list-style:none}
.footer-col li{font-size:12.5px;line-height:25px}
.col-links{width:201px}
.col-services{width:247px}
.col-news{width:330px}
.col-news p{font-size:12.5px;line-height:24px;width:240px}
.email-field{margin-top:14px;width:218px;height:32px;background:#5c6463;color:#eee;font-size:11.5px;padding:0 14px;display:flex;align-items:center}
.btn-submit{margin-top:12px;width:120px;height:32px;background:var(--sky);color:var(--white);font-weight:500;font-size:14px;display:flex;align-items:center;justify-content:center}
.col-contact li{line-height:24px}
.social{display:flex;gap:10px;margin-top:12px}
.social span{width:25px;height:25px;background:var(--teal);display:block}
.footer-bottom{border-top:1px solid #4d5655;height:56px;display:flex;align-items:center;justify-content:center;font-size:12px;color:var(--footer-text)}
.footer-bottom b{color:var(--teal);font-weight:400}
</style>
</head>
<body>

<section class="hero">
  <div class="hero-photo" role="img" aria-label="Photo of a smiling accountant working at a desk with files and a calculator"></div>
  <div class="hero-shade"></div>
  <header class="site-header">
    <a class="logo" href="#"><span class="logo-mark"></span><span class="logo-name">Dornaby Bookkeeping</span></a>
    <nav class="main-nav">
      <a class="active" href="#">Home</a>
      <a href="#">About Us</a>
      <a href="#">Services</a>
      <a href="#">Experience</a>
      <a href="#">Resources</a>
      <a href="#">Contact Us</a>
    </nav>
  </header>
  <div class="hero-copy">
    <h1>Accounting and Bookkeeping Services and Support</h1>
    <p>for small and growing organizations in San Diego North County.</p>
    <a class="btn-hero" href="#">Request your free Consultation
      <svg width="8" height="12" viewBox="0 0 8 12"><path d="M1.5 1l5 5-5 5" fill="none" stroke="#fff" stroke-width="1.8"/></svg></a>
  </div>
</section>

<section class="about">
  <div class="wrap">
    <div class="about-text">
      <h2 class="section-title">About <em>Dornaby Bookeeping</em></h2>
      <p>Lorem Ipsum is simply dummy text of the printing and typesetting industry. Lorem Ipsum has been the industry's standard dummy text ever since the 1500s, when an unknown printer took a galley of type and scrambled it to make a type specimen book.</p>
      <p>It has survived not only five centuries, but also the leap into electronic typesetting, remaining essentially unchanged. It was popularised in the 1960s with the release of Typeleaf sheets containing Lorem Ipsum passages, and more recently with desktop publishing software like Pagecraft Studio including versions of Lorem Ipsum.</p>
      <a class="btn-more" href="#">Learn more
        <svg width="6" height="10" viewBox="0 0 6 10"><path d="M1 1l4 4-4 4" fill="none" stroke="#555" stroke-width="1.4"/></svg></a>
    </div>
    <div class="about-divider"></div>
    <div class="features">
      <div class="feature">
        <div class="feature-icon"><svg width="28" height="28" viewBox="0 0 28 28"><path d="M3 13l5-5 6 3 6-3 5 5-8 8-3-3-3 3z" fill="none" stroke="#fff" stroke-width="2" stroke-linejoin="round"/></svg></div>
        <div><h3>Reliable</h3><p>It is a long established fact that a reader will be distracted by the readable content...</p></div>
      </div>
      <div class="feature">
        <div class="feature-icon"><svg width="28" height="28" viewBox="0 0 28 28"><path d="M22 10a9 9 0 0 0-16 0M6 18a9 9 0 0 0 16 0" fill="none" stroke="#fff" stroke-width="2"/><path d="M22 5v5h-5M6 23v-5h5" fill="none" stroke="#fff" stroke-width="2"/><circle cx="14" cy="14" r="3.5" fill="#fff"/></svg></div>
        <div><h3>Experienced</h3><p>It is a long established fact that a reader will be distracted by the readable content...</p></div>
      </div>
      <div class="feature">
        <div class="feature-icon"><svg width="28" height="28" viewBox="0 0 28 28"><circle cx="14" cy="14" r="10" fill="none" stroke="#fff" stroke-width="2"/><path d="M9 14l4 4 7-8" fill="none" stroke="#fff" stroke-width="2.4"/></svg></div>
        <div><h3>Qualified</h3><p>It is a long established fact that a reader will be distracted by the readable content...</p></div>
      </div>
    </div>
  </div>
</section>

<section class="services">
  <div class="wrap">
    <h2 class="section-title">Our Bookkeeping <em>Services</em></h2>
    <p class="section-sub">We provide bookkeeping services specializing in LedgerPro at your offices or remotely from ours</p>
    <div class="service-cards">
      <article class="service-card">
        <div class="service-photo photo-a" role="img" aria-label="Photo of a blue bookkeeping binder beside a calculator"></div>
        <h3>Bookkeeping Services</h3>
        <p>Simply dummy text of the printing and typesetting industry It is a long fact that a reader distracted...</p>
        <svg class="corner" width="30" height="30" viewBox="0 0 30 30"><path d="M30 0V30H0z" fill="#ddd"/><path d="M16 24h8v-8" fill="none" stroke="#999" stroke-width="1"/></svg>
      </article>
      <article class="service-card">
        <div class="service-photo photo-b" role="img" aria-label="Photo of hands working on a calculator and paperwork"></div>
        <h3>Accounting Services</h3>
        <p>Simply dummy text of the printing and typesetting industry It is a long fact that a reader distracted...</p>
        <svg class="corner" width="30" height="30" viewBox="0 0 30 30"><path d="M30 0V30H0z" fill="#ddd"/><path d="M16 24h8v-8" fill="none" stroke="#999" stroke-width="1"/></svg>
      </article>
      <article class="service-card">
        <div class="service-photo photo-c" role="img" aria-label="Photo of an advisor meeting with two clients"></div>
        <h3>Financial Advice</h3>
        <p>Simply dummy text of the printing and typesetting industry It is a long fact that a reader distracted...</p>
        <svg class="corner" width="30" height="30" viewBox="0 0 30 30"><path d="M30 0V30H0z" fill="#ddd"/><path d="M16 24h8v-8" fill="none" stroke="#999" stroke-width="1"/></svg>
      </article>
      <article class="service-card">
        <div class="service-photo photo-d" role="img" aria-label="Photo of a team reviewing charts on a tablet"></div>
        <h3>Management Accounting</h3>
        <p>Simply dummy text of the printing and typesetting industry It is a long fact that a reader distracted...</p>
        <svg class="corner" width="30" height="30" viewBox="0 0 30 30"><path d="M30 0V30H0z" fill="#ddd"/><path d="M16 24h8v-8" fill="none" stroke="#999" stroke-width="1"/></svg>
      </article>
    </div>
  </div>
</section>

<section class="cta-band">
  <div class="wrap">
    <p>Our people &amp; technology will take the pain out of your accounting &amp; bookkeeping, letting you get back to business.</p>
    <span class="cta-phone">Call Us: +1 760 555 0142</span>
    <a class="btn-contact" href="#">Contact us Now!
      <svg width="8" height="12" viewBox="0 0 8 12"><path d="M1.5 1l5 5-5 5" fill="none" stroke="#333" stroke-width="1.6"/></svg></a>
  </div>
</section>

<section class="clients">
  <div class="wrap">
    <h2 class="section-title">Our Clients <em>Love Us</em></h2>
    <p class="section-sub">It is a long established fact that a reader will be distracted content of a page when looking at its layout.</p>
    <div class="testimonials">
      <figure class="testimonial">
        <div class="avatar av-1" role="img" aria-label="Portrait photo of client"></div>
        <blockquote>“Lorem ipsum dolor sit amet, consectetur adipiscing elit, sed do eiusmod tempor incididunt ut labore et dolore magna aliqua. Ut enim veniam, quis nostrud ...”</blockquote>
        <div class="quote-rule"></div>
        <cite><b>Owen Marlow,</b> Medical</cite>
      </figure>
      <figure class="testimonial">
        <div class="avatar av-2" role="img" aria-label="Portrait photo of client"></div>
        <blockquote>“Lorem ipsum dolor sit amet, consectetur adipiscing elit, sed do eiusmod tempor incididunt ut labore et dolore magna aliqua. Ut enim veniam, quis nostrud ...”</blockquote>
        <div class="quote-rule"></div>
        <cite><b>Dana Whitlock,</b> Businessman</cite>
      </figure>
      <figure class="testimonial">
        <div class="avatar av-3" role="img" aria-label="Portrait photo of client"></div>
        <blockquote>“Lorem ipsum dolor sit amet, consectetur adipiscing elit, sed do eiusmod tempor incididunt ut labore et dolore magna aliqua. Ut enim veniam, quis nostrud ...”</blockquote>
        <div class="quote-rule"></div>
        <cite><b>Lena Carvajal,</b> The Law Office</cite>
      </figure>
    </div>
    <div class="partner-strip">
      <span class="partner"><i></i>Brightmere</span>
      <span class="partner"><i></i>Northvale</span>
      <span class="partner">Kestrel</span>
      <span class="partner"><i></i>Hollis</span>
      <span class="partner">Tamrock</span>
      <span class="partner">Ledgerly</span>
    </div>
  </div>
</section>

<footer class="site-footer">
  <div class="wrap footer-cols">
    <div class="footer-col col-links">
      <h4>Quick Link</h4>
      <ul><li>- Home</li><li>- About Us</li><li>- Services</li><li>- Experience</li><li>- Resources</li><li>- Contact Us</li></ul>
    </div>
    <div class="footer-col col-services">
      <h4>Services</h4>
      <ul><li>- Bookkeeping Services</li><li>- Accounting Services</li><li>- Financial Advice</li><li>- Management Accounting</li></ul>
    </div>
    <div class="footer-col col-news">
      <h4>Get our Newsletter</h4>
      <p>Sign Up now for more information about our company!</p>
      <div class="email-field">Enter Your Email</div>
      <div class="btn-submit">Submit</div>
    </div>
    <div class="footer-col col-contact">
      <h4>Services</h4>
      <ul><li>418 Palomar Way, Carlsbad,<br>CA, United States</li><li>Phone : +1 760 555 0198</li><li>Email : info@dornabybooks.com</li></ul>
      <div class="social"><span></span><span></span><span></span><span></span></div>
    </div>
  </div>
  <div class="footer-bottom">Copyright © 2016&nbsp;<b>Dornaby Bookkeeping</b>. All Rights Reserved</div>
</footer>

</body>
</html>
```